Defense Attorney Business Card Design Project/ Stationary

I am looking for a distinctive business card design for my solo law practice.
I practice criminal defense, both juvenile and adult, including DUI. I am a very experienced attorney with prior military experience. The design should convey a traditional, old school flair, but not be too stodgy or uptight. Some color. My logo should appear.
Updates

Project Deadline Extended Reason: I misunderstood how this project works and I was not prepared with my logo when this project ran the first time. Added Thursday, November 13, 2014

Project Deadline Extended
Reason: I was sent overseas on military duty last year, which interrupted this project. Thank you for your participation... I hope we can get this done this week! Thank you, Neil

Target Market(s)

Regular everyday people looking for strong, knowledgeable, authoritative representation while they are faced with criminal charges. Many have never been charged with a crime before. A reassuring air is therefore desired.

Industry/Entity Type

Business

Contact Information for Business Card

My information is:
Theodore M. Quill, Attorney at Law
785 Birch Avenue Suite 300
Oakland, California 94719
Tel: (510) 384-6125
Fax: (510) 391-7802
email: neilquilllaw@mailvine.example
web: www.neilquilllaw.example

Font styles to use
Serif
Sans Serif
Decorative

Colors
0255a3
ffffff

Requirements
Must have
• Sharp lines, bold elements. Conservative use of colors, such as deep blues, burgundy, grays for example.
• While my logo says "Neil Quill", it should be modified to show "Theodore M. Quill".
Should not have
• Cliche imagery such as scales of justice, gavels, Statue of Liberty, etc.

```html
<!DOCTYPE html>
<html lang="en">
<head>
<meta charset="utf-8">
<title>Theodore M. Quill — Business Cards</title>
<link rel="stylesheet" href="https://fonts.googleapis.com/css2?family=Cinzel:wght@400;600&family=Open+Sans:wght@400;600;700&display=swap">
<style>
  :root {
    --navy: #0b3f5c;
    --paper: #ffffff;
    --paper-shade: #eceeef;
    --ink: #2b2f33;
    --backdrop: #e7e3de;
  }
  * { box-sizing: border-box; margin: 0; padding: 0; }
  html, body { width: 1200px; height: 828px; overflow: hidden; }
  body {
    background: var(--backdrop);
    display: flex;
    align-items: center;
    justify-content: center;
    gap: 60px;
    font-family: "Open Sans", Arial, sans-serif;
  }
  .card {
    position: relative;
    width: 540px;
    height: 308px;
    background: linear-gradient(135deg, var(--paper) 0%, var(--paper) 55%, var(--paper-shade) 100%);
    box-shadow: 0 10px 24px rgba(0,0,0,0.18);
    overflow: hidden;
  }

  /* Brand block (shared) */
  .brand {
    position: absolute;
    display: flex;
    flex-direction: column;
  }
  .logo {
    display: flex;
    align-items: center;
    white-space: nowrap;
  }
  .logo-dot {
    border-radius: 50%;
    background: var(--navy);
    flex: none;
  }
  .logo-name {
    font-family: "Cinzel", Georgia, serif;
    font-weight: 600;
    color: var(--navy);
    line-height: 1;
  }
  .tagline {
    border-top: 1px solid var(--navy);
    font-family: "Cinzel", Georgia, serif;
    color: var(--navy);
    text-align: center;
    white-space: nowrap;
  }

  /* Front */
  .front .brand { left: 110px; top: 112px; }
  .front .logo { gap: 12px; }
  .front .logo-dot { width: 16px; height: 16px; }
  .front .logo-name { font-size: 32px; letter-spacing: 0.5px; }
  .front .tagline {
    margin: 14px 0 0 28px;
    padding-top: 6px;
    font-size: 13px;
    letter-spacing: 3px;
  }

  /* Back */
  .back .swoosh { position: absolute; inset: 0; }
  .back .brand { left: 24px; top: 122px; }
  .back .logo { gap: 8px; }
  .back .logo-dot { width: 11px; height: 11px; }
  .back .logo-name { font-size: 19px; }
  .back .tagline {
    margin: 10px 0 0 19px;
    padding-top: 5px;
    font-size: 10px;
    letter-spacing: 2.5px;
  }
  .contact {
    position: absolute;
    left: 276px;
    top: 24px;
    color: var(--ink);
  }
  .contact-name {
    font-weight: 700;
    font-size: 14px;
    color: var(--navy);
    text-transform: uppercase;
    letter-spacing: 0.5px;
    line-height: 1.4;
  }
  .contact-role { font-size: 10.5px; line-height: 1.4; margin-bottom: 8px; }
  .contact-address { font-size: 10px; line-height: 1.45; margin-bottom: 8px; }
  .contact-line {
    display: flex;
    align-items: center;
    gap: 7px;
    font-size: 10px;
    line-height: 1.65;
  }
  .contact-line svg { width: 10px; height: 10px; fill: var(--navy); flex: none; }
  .website {
    position: absolute;
    right: 20px;
    bottom: 14px;
    font-size: 11px;
    letter-spacing: 2.5px;
    color: var(--paper);
  }
</style>
</head>
<body>

  <section class="card front" aria-label="Business card front">
    <div class="brand">
      <div class="logo">
        <span class="logo-dot"></span>
        <span class="logo-name">Theodore M. Quill</span>
      </div>
      <div class="tagline">Attorney at Law</div>
    </div>
  </section>

  <section class="card back" aria-label="Business card back">
    <svg class="swoosh" viewBox="0 0 540 308" preserveAspectRatio="none" aria-hidden="true">
      <defs>
        <linearGradient id="silver" x1="0" y1="1" x2="1" y2="0">
          <stop offset="0" stop-color="#6f7479"/>
          <stop offset="0.45" stop-color="#e6e8ea"/>
          <stop offset="0.7" stop-color="#8a9096"/>
          <stop offset="1" stop-color="#3c4247"/>
        </linearGradient>
      </defs>
      <path d="M470 0 L540 0 L540 308 L110 308 C300 300 470 250 470 0 Z" fill="url(#silver)"/>
      <path d="M492 0 L540 0 L540 308 L150 308 C330 298 492 250 492 0 Z" fill="#ffffff"/>
      <path d="M500 0 L540 0 L540 308 L165 308 C340 298 500 255 500 0 Z" fill="#0b3f5c"/>
    </svg>

    <div class="brand">
      <div class="logo">
        <span class="logo-dot"></span>
        <span class="logo-name">Theodore M. Quill</span>
      </div>
      <div class="tagline">Attorney at Law</div>
    </div>

    <div class="contact">
      <p class="contact-name">Theodore M. Quill</p>
      <p class="contact-role">Managing Director</p>
      <p class="contact-address">785 Birch Avenue Suite 300<br>Oakland, California 94719</p>
      <p class="contact-line">
        <svg viewBox="0 0 10 10" aria-hidden="true"><path d="M0 2 H10 V8.5 H0 Z M0.6 2.4 L5 5.6 L9.4 2.4" stroke="#fff" stroke-width="0.8"/></svg>
        neilquilllaw@mailvine.example
      </p>
      <p class="contact-line">
        <svg viewBox="0 0 10 10" aria-hidden="true"><path d="M2 0.5 L3.6 2.6 L2.7 3.6 C3.3 5 4.9 6.6 6.4 7.3 L7.4 6.4 L9.5 8 L8.3 9.5 C4.5 9 1 5.5 0.5 1.7 Z"/></svg>
        Tel: (510) 384-6125
      </p>
      <p class="contact-line">
        <svg viewBox="0 0 10 10" aria-hidden="true"><path d="M2.5 0.5 H7.5 V3.5 H2.5 Z M0.5 3.5 H9.5 V8 H7.5 V9.5 H2.5 V8 H0.5 Z M3.3 6.5 V8.7 H6.7 V6.5 Z"/></svg>
        Fax: (510) 391-7802
      </p>
    </div>

    <p class="website">www.neilquilllaw.example</p>
  </section>

</body>
</html>
```